Floor Inspections and Consulting

We provide inspections and consulting services on various floor coverings, e.g. carpet, hardwood, etc. We also do expert witness work for attorneys due to floor covering failures. We current have a logo, just need it incorporated into a new design. I have examples of cards I have found on the internet that capture my attention and make a statement. I have included our original business card, which in my opinion is terrible, but it does have our logo on it.

```html
<!DOCTYPE html>
<html lang="en">
<head>
<meta charset="utf-8">
<title>Northvale Floor Review – Business Card</title>
<link rel="stylesheet" href="https://fonts.googleapis.com/css2?family=Cinzel:wght@700&family=Open+Sans:wght@400;600;700&display=swap">
<style>
  :root {
    --stage: #5a5a5c;
    --gold: #c4a55e;
    --gold-light: #d8c18a;
    --gold-deep: #a88a44;
    --black: #050505;
    --white: #ffffff;
    --silver-light: #f2f2f2;
    --silver-dark: #6f6f73;
    --muted: #d9d9d9;
  }
  * { box-sizing: border-box; margin: 0; padding: 0; }
  html, body {
    width: 1200px; height: 1126px; overflow: hidden;
    background: var(--stage);
    font-family: "Open Sans", sans-serif;
  }
  .card {
    position: absolute; left: 160px;
    width: 880px; height: 503px;
    overflow: hidden;
    box-shadow: 0 6px 18px rgba(0,0,0,.35);
  }
  .card--front { top: 40px; }
  .card--back { top: 583px; background: var(--black); }

  .sunburst {
    position: absolute; inset: 0;
    background: radial-gradient(circle at 50% 50%, var(--gold-light) 0%, var(--gold) 55%, var(--gold-deep) 100%);
  }
  .brand {
    position: absolute; display: flex; align-items: center; gap: 16px;
    font-family: "Open Sans", sans-serif; font-weight: 700;
    text-transform: uppercase; letter-spacing: 2px; line-height: 1.15;
  }
  .brand__dot { width: 46px; height: 46px; border-radius: 50%; flex: none; }
  .card--front .brand {
    left: 50%; top: 50%; transform: translate(-50%, -50%);
    color: var(--white); font-size: 34px;
  }
  .card--front .brand__dot { background: var(--white); width: 64px; height: 64px; }

  .waves { position: absolute; inset: 0; }

  .card--back .brand {
    left: 70px; top: 170px; width: 290px;
    color: var(--gold); font-size: 24px;
  }
  .card--back .brand__dot { background: var(--gold); }

  .divider {
    position: absolute; left: 405px; top: 120px;
    width: 2px; height: 200px; background: var(--gold);
  }
  .contact { position: absolute; left: 450px; top: 130px; }
  .contact__name {
    font-family: "Cinzel", serif; font-weight: 700;
    color: var(--gold); font-size: 30px; letter-spacing: 1px;
  }
  .contact__role { color: var(--muted); font-size: 19px; margin-top: -2px; }
  .contact__list { list-style: none; margin-top: 34px; }
  .contact__item {
    display: flex; align-items: center; gap: 12px;
    color: var(--white); font-size: 19px; line-height: 28px;
  }
  .contact__icon { width: 22px; height: 22px; flex: none; }

  .tagline {
    position: absolute; right: 52px; bottom: 22px;
    color: var(--white); font-weight: 600; font-size: 21px;
    line-height: 26px; text-align: left;
  }
</style>
</head>
<body>

<section class="card card--front">
  <div class="sunburst" role="img" aria-label="Gold sunburst rays background"></div>
  <div class="brand">
    <span class="brand__dot"></span>
    <span>Northvale<br>Floor Review</span>
  </div>
</section>

<section class="card card--back">
  <svg class="waves" viewBox="0 0 880 503" width="880" height="503" aria-hidden="true">
    <defs>
      <linearGradient id="silver" x1="0" x2="1" y1="0" y2="0">
        <stop offset="0" stop-color="var(--silver-dark)"/>
        <stop offset=".35" stop-color="var(--silver-light)"/>
        <stop offset=".7" stop-color="var(--silver-dark)"/>
        <stop offset="1" stop-color="var(--silver-light)"/>
      </linearGradient>
      <linearGradient id="goldband" x1="0" x2="1" y1="0" y2="1">
        <stop offset="0" stop-color="var(--gold-light)"/>
        <stop offset="1" stop-color="var(--gold-deep)"/>
      </linearGradient>
    </defs>
    <path d="M0,372 C160,452 330,442 500,422 C650,404 800,402 880,470 V503 H0 Z" fill="url(#goldband)"/>
    <path d="M0,352 C140,440 330,434 500,410 C650,390 800,390 880,462" fill="none" stroke="url(#silver)" stroke-width="10"/>
    <path d="M0,342 C120,410 260,428 420,420" fill="none" stroke="url(#silver)" stroke-width="4"/>
  </svg>

  <div class="brand">
    <span class="brand__dot"></span>
    <span>Northvale<br>Floor Review</span>
  </div>

  <div class="divider"></div>

  <div class="contact">
    <div class="contact__name">MARTIN DELACROIX</div>
    <div class="contact__role">President</div>
    <ul class="contact__list">
      <li class="contact__item">
        <svg class="contact__icon" viewBox="0 0 24 24"><circle cx="12" cy="12" r="12" fill="var(--gold)"/><path d="M8 6.5l2 2.5-1.2 1.5c.8 1.7 2 2.9 3.7 3.7l1.5-1.2 2.5 2-1.2 2.3C10.5 17 7 13.5 6.2 8z" fill="var(--black)"/></svg>
        555-014-2873
      </li>
      <li class="contact__item">
        <svg class="contact__icon" viewBox="0 0 24 24"><circle cx="12" cy="12" r="12" fill="var(--gold)"/><rect x="6" y="8" width="12" height="8.5" fill="var(--black)"/><path d="M6 8l6 5 6-5" fill="none" stroke="var(--gold)" stroke-width="1.2"/></svg>
        martin@northvalefloor.com
      </li>
      <li class="contact__item">
        <svg class="contact__icon" viewBox="0 0 24 24"><circle cx="12" cy="12" r="12" fill="var(--gold)"/><g fill="none" stroke="var(--black)" stroke-width="1.4"><circle cx="12" cy="12" r="6.5"/><ellipse cx="12" cy="12" rx="3" ry="6.5"/><path d="M5.5 12h13"/></g></svg>
        www.northvalefloor.com
      </li>
    </ul>
  </div>

  <p class="tagline">Certified Floor Covering<br>Inspections &amp; Consulting</p>
</section>

</body>
</html>
```